Veldmark Supplies Business Card

Professional business card that stand out to our potential customers. Front and back with clean modern design

Industry/Entity Type

Oil and gas

Contact Information for Business Card

Name, address, website , office phone and cell number

Requirements
Must have
• Editable files for each employee

```html
<!DOCTYPE html>
<html lang="en">
<head>
<meta charset="utf-8">
<title>Veldmark Supplies – Business Card</title>
<link href="https://fonts.googleapis.com/css2?family=Figtree:wght@400;500;700;800&display=swap" rel="stylesheet">
<style>
  :root {
    --stage: #e3e4e3;
    --cyan: #04aed2;
    --red: #f2141b;
    --white: #ffffff;
    --card-radius: 44px;
  }
  * { box-sizing: border-box; margin: 0; padding: 0; }
  html, body { width: 1200px; height: 900px; overflow: hidden; }
  body {
    background: var(--stage);
    font-family: "Figtree", Arial, sans-serif;
    position: relative;
  }
  .card {
    position: absolute;
    top: 39px;
    width: 466px;
    height: 815px;
    border-radius: var(--card-radius);
    overflow: hidden;
  }
  .card-back { left: 133px; background: var(--cyan); }
  .back-pattern {
    position: absolute; inset: 0;
    background: linear-gradient(180deg, #f01a1e 0%, #c93344 35%, #7a5a72 55%, #3f8aa8 75%, var(--cyan) 100%);
    opacity: .85;
  }
  .card-front { left: 615px; background: var(--cyan); }
  .front-top {
    position: absolute; left: 0; top: 0; width: 100%; height: 261px;
    background: var(--white);
  }
  .brand-bar {
    position: absolute; left: 33px; top: 29px; width: 398px; height: 44px;
    display: flex; align-items: center; justify-content: center; gap: 12px;
  }
  .brand-square { width: 22px; height: 22px; background: var(--red); }
  .brand-name {
    font-weight: 800; font-size: 30px; letter-spacing: 1px;
    color: var(--red); text-transform: uppercase;
  }
  .brand-disc {
    position: absolute; left: 133px; top: 181px; width: 200px; height: 200px;
    border-radius: 50%; background: var(--white);
  }
  .centered { position: absolute; left: 0; width: 100%; text-align: center; color: var(--white); }
  .person-name { top: 432px; font-size: 33px; font-weight: 800; letter-spacing: .5px; }
  .person-title {
    top: 476px; font-size: 21px; font-weight: 500;
    display: flex; align-items: center; justify-content: center; gap: 12px;
  }
  .person-title::before, .person-title::after {
    content: ""; width: 84px; height: 2px; background: var(--white);
  }
  .contact-icons {
    position: absolute; top: 530px; left: 128px; width: 207px; height: 36px;
    display: flex; justify-content: space-between;
  }
  .contact-icon {
    width: 37px; height: 36px; background: var(--red);
    display: flex; align-items: center; justify-content: center;
  }
  .contact-list { top: 585px; font-size: 21px; line-height: 29.5px; }
  .divider {
    position: absolute; left: 117px; top: 719px; width: 231px; height: 1px;
    background: rgba(255,255,255,.85);
  }
  .address { top: 729px; font-size: 21px; line-height: 30px; }
</style>
</head>
<body>
  <section class="card card-back">
    <div class="back-pattern" role="img" aria-label="Repeating pattern of the company mark, fading from red at the top to blue at the bottom"></div>
  </section>

  <section class="card card-front">
    <div class="front-top"></div>
    <div class="brand-bar">
      <span class="brand-square"></span>
      <span class="brand-name">Veldmark Supplies</span>
    </div>
    <div class="brand-disc"></div>

    <h1 class="centered person-name">DARA KELLWYN</h1>
    <p class="centered person-title">President</p>

    <div class="contact-icons">
      <span class="contact-icon" aria-label="Office phone">
        <svg width="24" height="20" viewBox="0 0 24 20"><path d="M2 8c0-4 4-6 10-6s10 2 10 6l-4 1-1-3H7L6 9z" fill="#fff"/><rect x="5" y="10" width="14" height="8" rx="2" fill="#fff"/></svg>
      </span>
      <span class="contact-icon" aria-label="Cell phone">
        <svg width="14" height="26" viewBox="0 0 14 26"><rect x="1" y="1" width="12" height="24" rx="2" fill="none" stroke="#fff" stroke-width="2"/><circle cx="7" cy="21" r="1.5" fill="#fff"/></svg>
      </span>
      <span class="contact-icon" aria-label="Email">
        <svg width="26" height="18" viewBox="0 0 26 18"><rect x="1" y="1" width="24" height="16" fill="none" stroke="#fff" stroke-width="2"/><path d="M1 1l12 9 12-9" fill="none" stroke="#fff" stroke-width="2"/></svg>
      </span>
      <span class="contact-icon" aria-label="Website">
        <svg width="24" height="24" viewBox="0 0 24 24"><circle cx="12" cy="12" r="10" fill="none" stroke="#fff" stroke-width="2"/><ellipse cx="12" cy="12" rx="4" ry="10" fill="none" stroke="#fff" stroke-width="1.5"/><path d="M2 12h20" stroke="#fff" stroke-width="1.5"/></svg>
      </span>
    </div>

    <p class="centered contact-list">555-014-2870<br>555-010-3344<br>info@veldmarksupplies.com<br>www.veldmarksupplies.com</p>
    <div class="divider"></div>
    <p class="centered address">4820 Larkspur Ave, Ste<br>210, Midvale, TX 75220</p>
  </section>
</body>
</html>
```